Business Card Design

Business Card for professional consulting firm working with large financial institutions.

Target Market(s)

Executive buyers

Industry/Entity Type

Banking

Contact Information for Business Card

Mild creativity wanted. Not boring, but do elaborate artwork.

Font styles to use
Serif
Sans Serif

Colors

Designer to choose colors to be used in the design.

Requirements
Must have
• Standard business card features - company name, individual name, telephone, website, email, locations.
Nice to have
• Two colors
Should not have
• too many colors, fancy printing, cartoons.

```html
<!DOCTYPE html>
<html lang="en">
<head>
<meta charset="utf-8">
<title>k4advisors — Business Card</title>
<link href="https://fonts.googleapis.com/css2?family=Tinos:wght@400;700&display=swap" rel="stylesheet">
<style>
  :root {
    --stage: #e6e4e1;
    --ink: #0c0c0c;
    --paper: #f4f4f4;
    --grey: #a9a9a9;
    --grey-soft: #c9c9c9;
    --text: #2a2a2a;
    --white: #ffffff;
  }
  * { margin: 0; padding: 0; box-sizing: border-box; }
  html, body {
    width: 1200px; height: 886px; overflow: hidden;
    background: var(--stage);
    font-family: "Tinos", "Times New Roman", serif;
  }
  .canvas { position: relative; width: 1200px; height: 886px; }

  .card {
    position: absolute;
    width: 560px; height: 320px;
    border-radius: 22px;
    overflow: hidden;
    box-shadow: 0 10px 28px rgba(0,0,0,0.22);
  }

  /* Back side */
  .card--back {
    left: 60px; top: 110px;
    background: linear-gradient(160deg, #1d1d1d 0%, var(--ink) 60%);
    display: flex; align-items: center; justify-content: center;
  }
  .card--back .brand-name {
    color: var(--white);
    font-size: 44px;
  }

  /* Front side */
  .card--front {
    left: 580px; top: 450px;
    background: var(--paper);
  }
  .card__wave { position: absolute; left: 0; top: 0; width: 560px; height: 320px; }
  .card--front .brand-name {
    position: absolute; left: 48px; top: 92px;
    color: var(--text);
    font-size: 30px;
  }
  .card__divider {
    position: absolute; left: 300px; top: 66px;
    width: 1px; height: 140px;
    background: var(--grey);
  }
  .contact {
    position: absolute; left: 322px; top: 66px;
    color: var(--text);
    font-size: 13px; line-height: 15px;
  }
  .contact__name { font-size: 22px; font-weight: 700; line-height: 22px; color: var(--ink); }
  .contact__title { font-size: 16px; line-height: 18px; color: var(--grey); margin-bottom: 4px; }
  .contact__block + .contact__block { margin-top: 8px; }

  .brand-name { font-family: "Tinos", "Times New Roman", serif; font-weight: 400; letter-spacing: 0.5px; }
</style>
</head>
<body>
<main class="canvas">

  <section class="card card--back" aria-label="Card back">
    <span class="brand-name">k4advisors</span>
  </section>

  <section class="card card--front" aria-label="Card front">
    <svg class="card__wave" viewBox="0 0 560 320" aria-hidden="true">
      <path d="M0,232 C140,262 360,270 560,262 L560,320 L0,320 Z" fill="var(--ink)"/>
      <path d="M0,210 C150,244 370,254 560,246 L560,262 C360,270 140,262 0,232 Z" fill="var(--white)"/>
      <path d="M0,206 C150,240 370,250 560,242" fill="none" stroke="var(--grey)" stroke-width="3"/>
      <path d="M40,228 C180,258 380,264 560,256" fill="none" stroke="var(--grey-soft)" stroke-width="6"/>
    </svg>

    <span class="brand-name">k4advisors</span>
    <div class="card__divider"></div>

    <div class="contact">
      <div class="contact__name">Daniel Reyes</div>
      <div class="contact__title">Managing Director</div>
      <div class="contact__block">
        k4advisors<br>
        2140 Harbor View Road<br>
        Juneau, Alaska 99801
      </div>
      <div class="contact__block">
        907 555 0184<br>
        info@k4advisors.com<br>
        www.k4advisors.com
      </div>
    </div>
  </section>

</main>
</body>
</html>
```